Business card design for Automotive workshop

We need a business card for a new automotive repair and tyre shop called Keelstone Prime Automotive located in New Zealand. We are a clean, modern and fresh workshop and company.

Front needs to feature logo,
my name:
Marlo Fenwicke (director)

Address:
48 Tarn Lane
Whitianga 3510

Phone: 07 594 2713
Mobile: 027 451 9362
Email: office@keelstoneautomotive.example.nz
Website: keelstoneautomotive.example.nz

Back needs to feature an area to write down appointment details, date and time.

Also feature a list of jobs and work we do such as,
Vehicle Servicing
All Mechanical Repairs
Warrant of Fitness
Tyres & Wheel Alignments
Automotive Diagnostics
Automotive Parts & Supplies

```html
<!DOCTYPE html>
<html lang="en">
<head>
<meta charset="utf-8">
<title>Keelstone Prime Automotive – Business Card</title>
<link rel="stylesheet" href="https://fonts.googleapis.com/css2?family=Roboto:wght@400;500;700&display=swap">
<style>
  :root {
    --navy: #0c1530;
    --navy-ring: #2d3450;
    --red: #e32227;
    --red-deep: #7a2632;
    --red-mid: #a8262e;
    --ink: #111111;
    --white: #ffffff;
    --stage-light: #525252;
    --stage-dark: #262626;
  }
  * { box-sizing: border-box; margin: 0; padding: 0; }
  html, body { width: 1200px; height: 750px; overflow: hidden; }
  body {
    position: relative;
    background: radial-gradient(ellipse at 50% 30%, var(--stage-light) 0%, var(--stage-dark) 75%);
    font-family: "Roboto", Arial, sans-serif;
  }
  .card {
    position: absolute;
    top: 186px;
    width: 560px;
    height: 329px;
    border-radius: 26px;
    overflow: hidden;
    box-shadow: 0 4px 10px rgba(0,0,0,0.45);
  }
  .card-front { left: 38px; background: var(--white); }
  .card-back { left: 610px; background: var(--navy); }
  .card-art { position: absolute; inset: 0; width: 100%; height: 100%; }

  .brand-name {
    position: absolute;
    color: var(--red);
    font-weight: 700;
    font-size: 19px;
    line-height: 1.05;
    letter-spacing: 1.5px;
    text-transform: uppercase;
  }
  .card-front .brand-name { left: 308px; top: 144px; width: 210px; text-align: center; }
  .card-back .brand-name { left: 37px; top: 60px; width: 220px; }

  .holder { position: absolute; left: 0; top: 76px; }
  .holder-tab {
    position: absolute; left: 0; top: 2px;
    width: 48px; height: 29px;
    background: var(--red);
    border-radius: 0 15px 15px 0;
  }
  .holder-tab svg { position: absolute; right: 2px; top: 2px; }
  .holder-name {
    position: absolute; left: 52px; top: 0;
    font-size: 24px; font-weight: 700; color: var(--ink); white-space: nowrap;
  }
  .holder-role {
    position: absolute; left: 46px; top: 32px;
    font-size: 19px; color: var(--ink); white-space: nowrap;
  }

  .contacts { position: absolute; left: 0; top: 169px; list-style: none; }
  .contact {
    position: relative; height: 24px;
    display: flex; align-items: center;
    font-size: 14px; color: var(--ink); white-space: nowrap;
  }
  .contact-tab {
    width: 38px; height: 17px; background: var(--red);
    border-radius: 0 9px 9px 0; position: relative; margin-right: 2px; flex: none;
  }
  .contact-tab svg { position: absolute; right: 0; top: -1px; }
  .contact-email { font-size: 13px; }

  .services { position: absolute; left: 28px; top: 120px; list-style: none; }
  .service {
    display: flex; align-items: center; gap: 8px;
    height: 23.8px; color: var(--white); font-size: 14.5px; letter-spacing: 0.2px;
  }
  .dot { width: 8px; height: 8px; border-radius: 50%; background: var(--red); flex: none; }

  .appointment {
    position: absolute; left: 28px; top: 280px;
    display: flex; align-items: center; color: var(--white); font-size: 14.5px;
  }
  .appointment .field { display: flex; align-items: center; gap: 4px; }
  .appointment .write-line {
    width: 182px; height: 3px; background: var(--white); margin: 5px 0 0 6px;
  }
  .appointment .field + .field { margin-left: 34px; }
</style>
</head>
<body>

<section class="card card-front" aria-label="Card front">
  <svg class="card-art" viewBox="0 0 560 329" aria-hidden="true">
    <circle cx="486" cy="164" r="208" fill="var(--navy-ring)"/>
    <circle cx="477" cy="164" r="184" fill="var(--navy)"/>
  </svg>

  <div class="brand-name">Keelstone Prime<br>Automotive</div>

  <div class="holder">
    <span class="holder-tab">
      <svg width="25" height="25" viewBox="0 0 25 25" aria-hidden="true">
        <circle cx="12.5" cy="12.5" r="12" fill="var(--ink)"/>
        <circle cx="12.5" cy="8" r="3" fill="var(--red)"/>
        <rect x="9" y="12" width="7" height="8" rx="2" fill="var(--red)"/>
      </svg>
    </span>
    <h1 class="holder-name">Marlo Fenwicke</h1>
    <p class="holder-role">(Managing director)</p>
  </div>

  <ul class="contacts">
    <li class="contact"><span class="contact-tab"><svg width="19" height="19" viewBox="0 0 19 19" aria-hidden="true"><circle cx="9.5" cy="9.5" r="9" fill="var(--ink)"/><path d="M6 5 l2 0 1 3 -1.5 1 a6 6 0 0 0 3 3 l1 -1.5 3 1 0 2 c-5 1 -9 -4 -8.5 -8.5z" fill="var(--red)"/></svg></span>027 451 9362</li>
    <li class="contact"><span class="contact-tab"><svg width="19" height="19" viewBox="0 0 19 19" aria-hidden="true"><circle cx="9.5" cy="9.5" r="9" fill="var(--ink)"/><rect x="5" y="8" width="9" height="6" rx="1" fill="var(--red)"/><path d="M4 8 q5.5 -4 11 0" stroke="var(--red)" stroke-width="1.6" fill="none"/></svg></span>07 594 2713</li>
    <li class="contact contact-email"><span class="contact-tab"><svg width="19" height="19" viewBox="0 0 19 19" aria-hidden="true"><circle cx="9.5" cy="9.5" r="9" fill="var(--ink)"/><rect x="5" y="6.5" width="9" height="6" fill="var(--red)"/><path d="M5 6.5 l4.5 3.5 4.5 -3.5" stroke="var(--ink)" stroke-width="1" fill="none"/></svg></span>office@keelstoneautomotive.example.nz</li>
    <li class="contact"><span class="contact-tab"><svg width="19" height="19" viewBox="0 0 19 19" aria-hidden="true"><circle cx="9.5" cy="9.5" r="9" fill="var(--ink)"/><circle cx="9.5" cy="9.5" r="5" fill="none" stroke="var(--red)" stroke-width="1.3"/><path d="M4.5 9.5 h10 M9.5 4.5 v10" stroke="var(--red)" stroke-width="1.1"/></svg></span>keelstoneautomotive.example.nz</li>
    <li class="contact"><span class="contact-tab"><svg width="19" height="19" viewBox="0 0 19 19" aria-hidden="true"><circle cx="9.5" cy="9.5" r="9" fill="var(--ink)"/><path d="M4.5 10 l5 -5 5 5 h-1.5 v4 h-7 v-4z" fill="var(--red)"/></svg></span>48 Tarn Lane Whitianga 3510</li>
  </ul>
</section>

<section class="card card-back" aria-label="Card back">
  <svg class="card-art" viewBox="0 0 562 329" aria-hidden="true">
    <circle cx="462" cy="86" r="118" fill="var(--red-deep)"/>
    <circle cx="476" cy="84" r="108" fill="var(--red-mid)"/>
    <circle cx="492" cy="76" r="98" fill="var(--red)"/>
  </svg>

  <div class="brand-name">Keelstone Prime<br>Automotive</div>

  <ul class="services">
    <li class="service"><span class="dot"></span>Vehicle Servicing</li>
    <li class="service"><span class="dot"></span>All Mechanical Repairs</li>
    <li class="service"><span class="dot"></span>Warrant of Fitness</li>
    <li class="service"><span class="dot"></span>Tyres &amp; Wheel Alignments</li>
    <li class="service"><span class="dot"></span>Automotive Parts &amp; Supplies</li>
    <li class="service"><span class="dot"></span>Automotive Diagnostics</li>
  </ul>

  <div class="appointment">
    <div class="field"><span class="dot"></span>Date<span class="write-line"></span></div>
    <div class="field"><span class="dot"></span>Time<span class="write-line"></span></div>
  </div>
</section>

</body>
</html>
```